Harborline Renewal Business Card Design

Professional and clean design. The design colors should flow with the logo. Two-sided card with the website on the back which is:

www.HarborlineRenewal.example.

"Specializing in Water Damage Restoration"

On the front I need the name, email, phone, and logo.

Name: Darnell Quisby
Email: Darnell@HarborlineRenewal.example
Phone: 555-318-2046 for now

I only have the Preview and Thumbnail right now but should have the source files uploaded within a day or two.

Target Market(s)

Flood victims, home owners with water damage from busted pipes etc...

Industry/Entity Type

Business

Contact Information for Business Card

Name: Darnell Quisby

Font styles to use
Serif
Sans Serif

Requirements
Must have
• Business Card Details Info

```html
<!DOCTYPE html>
<html lang="en">
<head>
<meta charset="utf-8">
<title>Harborline Renewal Business Card</title>
<link rel="stylesheet" href="https://fonts.googleapis.com/css2?family=Cinzel:wght@400;600&family=Open+Sans:wght@400;600&display=swap">
<style>
  :root {
    --bg: #ece9e4;
    --blue-deep: #1f8fd0;
    --blue-mid: #3aa6e0;
    --blue-light: #7cc7ef;
    --blue-pale: #a9dcf6;
    --white: #ffffff;
    --card-shadow: rgba(30, 40, 60, 0.25);
    --logo-blue: #2c95cf;
  }
  * { margin: 0; padding: 0; box-sizing: border-box; }
  html, body { width: 1200px; height: 843px; overflow: hidden; }
  body {
    background: var(--bg);
    position: relative;
    font-family: "Open Sans", Arial, sans-serif;
  }
  .card {
    position: absolute;
    width: 520px;
    height: 297px;
    border-radius: 22px;
    overflow: hidden;
    box-shadow: 0 14px 30px var(--card-shadow);
  }
  /* Back side */
  .card-back {
    left: 60px;
    top: 273px;
    background: linear-gradient(120deg, var(--blue-deep) 0%, var(--blue-mid) 55%, var(--blue-light) 100%);
  }
  .card-back .deco { position: absolute; inset: 0; }
  .back-name {
    position: absolute;
    left: 34px;
    top: 196px;
    font-family: "Cinzel", Georgia, serif;
    font-weight: 600;
    font-size: 30px;
    letter-spacing: 1px;
    color: var(--white);
  }
  .back-tagline {
    position: absolute;
    left: 34px;
    top: 242px;
    font-size: 13.5px;
    font-weight: 600;
    color: var(--white);
  }
  /* Front side */
  .card-front {
    left: 620px;
    top: 273px;
    background: linear-gradient(160deg, #ffffff 0%, #f4f6f8 60%, #e6eaee 100%);
  }
  .card-front .panel { position: absolute; inset: 0; }
  .contact {
    position: absolute;
    left: 28px;
    top: 130px;
    color: var(--white);
  }
  .contact-name {
    font-family: "Cinzel", Georgia, serif;
    font-size: 18px;
    letter-spacing: 0.5px;
    margin-bottom: 8px;
  }
  .contact-list { list-style: none; }
  .contact-list li {
    display: flex;
    align-items: center;
    gap: 9px;
    font-size: 11.5px;
    line-height: 20px;
  }
  .contact-list svg { width: 11px; height: 11px; flex: none; }
  .brand {
    position: absolute;
    right: 30px;
    top: 64px;
    width: 200px;
    text-align: center;
  }
  .brand-dot {
    width: 46px;
    height: 46px;
    border-radius: 50%;
    background: var(--logo-blue);
    margin: 0 auto 12px;
  }
  .brand-name {
    font-family: "Cinzel", Georgia, serif;
    font-weight: 600;
    font-size: 25px;
    line-height: 28px;
    color: var(--logo-blue);
    letter-spacing: 1px;
  }
</style>
</head>
<body>

<section class="card card-back" aria-label="Card back">
  <svg class="deco" viewBox="0 0 520 297" aria-hidden="true">
    <circle cx="430" cy="70" r="120" fill="none" stroke="#ffffff" stroke-width="16"/>
    <path d="M0 0 H230 Q150 150 0 200 Z" fill="#ffffff" opacity="0.08"/>
  </svg>
  <div class="back-name">HARBORLINE RENEWAL</div>
  <div class="back-tagline">Specializing in Water Damage Restoration</div>
</section>

<section class="card card-front" aria-label="Card front">
  <svg class="panel" viewBox="0 0 520 297" aria-hidden="true">
    <defs>
      <linearGradient id="panelShade" x1="0" y1="0" x2="1" y2="1">
        <stop offset="0" stop-color="#5bb8ea" stop-opacity="0.6"/>
        <stop offset="1" stop-color="#1f8fd0" stop-opacity="0.6"/>
      </linearGradient>
    </defs>
    <path d="M0 86 Q318 26 352 297 H0 Z" fill="var(--blue-pale)"/>
    <path d="M0 100 Q300 40 330 297 H0 Z" fill="var(--blue-mid)"/>
    <path d="M0 100 Q300 40 330 297 H0 Z" fill="url(#panelShade)"/>
  </svg>
  <div class="contact">
    <div class="contact-name">DARNELL QUISBY</div>
    <ul class="contact-list">
      <li>
        <svg viewBox="0 0 12 12" aria-hidden="true"><path d="M2.5 1 L4.5 1 L5 3.5 L3.8 4.5 Q5 7 7.5 8.2 L8.5 7 L11 7.5 L11 9.5 Q10 11 8 10.7 Q2 9 1.2 3 Q1 1.5 2.5 1 Z" fill="#fff"/></svg>
        555-318-2046 for now
      </li>
      <li>
        <svg viewBox="0 0 12 12" aria-hidden="true"><rect x="0.5" y="2" width="11" height="8" fill="#fff"/><path d="M0.5 2 L6 6.5 L11.5 2" fill="none" stroke="#3aa6e0" stroke-width="1"/></svg>
        Darnell@HarborlineRenewal.example
      </li>
      <li>
        <svg viewBox="0 0 12 12" aria-hidden="true"><circle cx="6" cy="6" r="5.5" fill="#fff"/><path d="M0.5 6 H11.5 M6 0.5 Q2.5 6 6 11.5 M6 0.5 Q9.5 6 6 11.5" fill="none" stroke="#3aa6e0" stroke-width="0.9"/></svg>
        www.HarborlineRenewal.example
      </li>
    </ul>
  </div>
  <div class="brand">
    <div class="brand-dot"></div>
    <div class="brand-name">HARBORLINE<br>RENEWAL</div>
  </div>
</section>

</body>
</html>
```